Resposive web site in 4 languages + image gallery + logo design

We need a web page, which will work on all devices.
I have uploaded web page concept.
Company name: Praxelun
Industry/Entity Type
It Company
Logo Text
quality matters
Coding
Coded - Design and coding required
Number of Pages Required
1 page

```html
<!DOCTYPE html>
<html lang="en">
<head>
<meta charset="utf-8">
<title>Praxelun</title>
<link href="https://fonts.googleapis.com/css2?family=Roboto+Condensed:wght@400;700&family=Open+Sans:wght@400;600&display=swap" rel="stylesheet">
<style>
:root{
  --green:#1f8c22;
  --green-dark:#137015;
  --footer-green:#178a1a;
  --text:#2f2f2f;
  --muted:#555;
  --white:#fff;
  --hero-dark:#2b241f;
  --contact-dark:#26221f;
}
*{margin:0;padding:0;box-sizing:border-box}
html,body{width:1200px;height:3010px;overflow:hidden;background:var(--white)}
body{position:relative;font-family:"Open Sans",Arial,sans-serif;color:var(--text)}
.abs{position:absolute}
.heading{font-family:"Roboto Condensed",Arial,sans-serif}

/* Hero */
.hero{left:0;top:0;width:1200px;height:630px;background:radial-gradient(ellipse at 40% 45%,#6b5a4a 0%,#3e342c 45%,var(--hero-dark) 100%)}
.brand{left:100px;top:32px;display:flex;flex-direction:column;align-items:center;gap:6px}
.brand-mark{width:56px;height:56px;border-radius:50%;background:var(--green)}
.brand-name{font-family:"Open Sans",sans-serif;font-weight:600;font-size:28px;color:var(--white)}
.nav{top:56px;display:flex;font-family:"Roboto Condensed",sans-serif;font-size:15px;color:var(--white);letter-spacing:.5px}
.lang{left:940px;top:50px;width:112px;height:32px;background:var(--white);border-radius:2px;font-size:10px;color:#999;display:flex;align-items:center;padding-left:10px;gap:6px}
.lang-flag{width:14px;height:9px;background:#3a4e9a}
.social-circle{left:1066px;top:50px;width:32px;height:32px;border-radius:50%;background:var(--white)}
.hero-title{left:0;width:1200px;top:322px;text-align:center;font-weight:700;font-size:38px;color:var(--white)}
.btn-quote{left:518px;top:392px;width:164px;height:42px;border:1.5px solid var(--white);color:var(--white);font-family:"Roboto Condensed",sans-serif;font-weight:700;font-size:17px;display:flex;align-items:center;justify-content:center}

/* Services */
.section-title{left:0;width:1200px;text-align:center;font-size:32px;color:#222}
.service-photo{border:4px solid #222;box-shadow:0 0 0 1px #bbb}
.service-photo::after{content:"";position:absolute;inset:10px;border:3px solid var(--white)}
.service-title{font-size:30px;color:#222}
.service-text{width:520px;font-size:11.5px;line-height:24px;color:var(--muted)}
.service-text p+p{margin-top:6px}
.service-list{display:grid;grid-template-columns:128px 200px;row-gap:8px;font-family:"Roboto Condensed",sans-serif;font-size:13.5px;color:#333;list-style:none}
.service-list li{display:flex;align-items:center;gap:14px}
.service-list svg{width:11px;height:11px;flex:none}

/* About */
.about{left:0;top:1908px;width:1200px;height:454px;background:linear-gradient(135deg,#24952a,var(--green) 55%,#1a7f1e)}
.about-people{left:140px;top:1962px;width:440px;height:400px;background:linear-gradient(180deg,#8b8f96,#5a6470 60%,#2f3a4a)}
.about-title{left:602px;top:2024px;font-size:30px;color:var(--white)}
.about-text{left:602px;top:2072px;width:500px;font-size:11.5px;line-height:22px;color:var(--white)}
.about-text p+p{margin-top:10px}
.about-sign{left:602px;top:2226px;color:var(--white)}
.about-sign .quote{font-family:"Roboto Condensed",sans-serif;font-size:23px}
.about-sign .name{font-size:15px;margin-top:4px}

/* Contact */
.contact{left:0;top:2362px;width:1200px;height:538px;background:radial-gradient(ellipse at 30% 50%,#3d342d,var(--contact-dark) 70%)}
.contact-title{top:2426px;color:var(--white)}
.info-title{left:140px;top:2504px;font-size:24px;color:var(--white)}
.info-row{left:140px;display:flex;align-items:center;gap:28px;font-size:12px;line-height:22px;color:var(--white)}
.info-icon{width:36px;height:36px;border:2px solid var(--white);border-radius:50%;display:flex;align-items:center;justify-content:center;flex:none}
.social-title{left:140px;top:2752px;font-family:"Roboto Condensed",sans-serif;font-weight:700;font-size:16px;color:var(--white)}
.social-icons{left:140px;top:2794px;display:flex;gap:12px}
.social-icons span{width:24px;height:24px;background:var(--white);border-radius:3px}
.field{background:var(--white);font-size:11px;color:#999;padding:7px 10px}
.btn-submit{left:968px;top:2778px;width:80px;height:32px;background:var(--green-dark);color:var(--white);font-family:"Roboto Condensed",sans-serif;font-weight:700;font-size:13px;display:flex;align-items:center;justify-content:center}

/* Footer */
.footer{left:0;top:2900px;width:1200px;height:110px;background:var(--footer-green);color:var(--white);text-align:center}
.footer-nav{margin-top:28px;font-family:"Roboto Condensed",sans-serif;font-size:12px;letter-spacing:.5px}
.footer-nav span{margin:0 8px}
.footer-copy{margin-top:10px;font-size:12px}
</style>
</head>
<body>

<!-- Hero -->
<section class="abs hero" role="img" aria-label="Craftsman carving a wooden baluster with a chisel"></section>
<div class="abs brand"><span class="brand-mark"></span><span class="brand-name">Praxelun</span></div>
<span class="abs nav" style="left:608px">SERVICES</span>
<span class="abs nav" style="left:714px">ABOUT US</span>
<span class="abs nav" style="left:822px">CONTACT US</span>
<div class="abs lang"><span class="lang-flag"></span>ENGLISH<span style="margin-left:auto;margin-right:12px">⌄</span></div>
<span class="abs social-circle"></span>
<svg class="abs" style="left:34px;top:322px" width="34" height="60" viewBox="0 0 34 60"><path d="M30 2 L4 30 L30 58" fill="none" stroke="#fff" stroke-width="1.5"/></svg>
<svg class="abs" style="left:1132px;top:322px" width="34" height="60" viewBox="0 0 34 60"><path d="M4 2 L30 30 L4 58" fill="none" stroke="#fff" stroke-width="1.5"/></svg>
<h1 class="abs heading hero-title">ARE YOU INTERESTED IN AN ESTIMATE?</h1>
<a class="abs btn-quote">GET A QUOTE</a>

<!-- Services -->
<h2 class="abs heading section-title" style="top:680px">OUR SERVICES</h2>

<div class="abs service-photo" role="img" aria-label="Hands planing a piece of wood on a workbench" style="left:108px;top:762px;width:432px;height:330px;background:linear-gradient(135deg,#5b4433,#a2805e 55%,#3d2e24)"></div>
<h3 class="abs heading service-title" style="left:576px;top:792px">WOODWORKS</h3>
<div class="abs service-text" style="left:576px;top:836px"><p>Timber is, in essence, a natural and warm material. Wood is also relatively durable and easy to work with, which has made it a favourite of builders throughout history. Our goal is to offer suitable products and quality furniture with installation and after-sales service to all of our clients. In order to achieve this, we're ready to help our clients in all stages of construction from design to production and maintenance.</p></div>
<ul class="abs service-list" style="left:578px;top:982px">
  <li><svg viewBox="0 0 12 12"><circle cx="6" cy="6" r="5" fill="none" stroke="#1f8c22" stroke-width="2"/></svg>FURNITURE</li>
  <li><svg viewBox="0 0 12 12"><circle cx="6" cy="6" r="5" fill="none" stroke="#1f8c22" stroke-width="2"/></svg>STAIRCASES</li>
  <li><svg viewBox="0 0 12 12"><circle cx="6" cy="6" r="5" fill="none" stroke="#1f8c22" stroke-width="2"/></svg>WINDOWS</li>
  <li><svg viewBox="0 0 12 12"><circle cx="6" cy="6" r="5" fill="none" stroke="#1f8c22" stroke-width="2"/></svg>WOODCARVING</li>
  <li><svg viewBox="0 0 12 12"><circle cx="6" cy="6" r="5" fill="none" stroke="#1f8c22" stroke-width="2"/></svg>DOORS</li>
  <li><svg viewBox="0 0 12 12"><circle cx="6" cy="6" r="5" fill="none" stroke="#1f8c22" stroke-width="2"/></svg>GRAINING</li>
</ul>

<h3 class="abs heading service-title" style="left:108px;top:1148px">STONEWORKS</h3>
<div class="abs service-text" style="left:108px;top:1192px"><p>The natural stone found in the ground has been used in construction for centuries because of its durability. A structure built by a skilled craftsman from natural stone is unique, genuine and durable, and perfect for our bracing climate.</p><p>Our experienced craftsmen are ready to help you in all stages of construction from planning to completion.</p></div>
<ul class="abs service-list" style="left:110px;top:1336px">
  <li><svg viewBox="0 0 12 12"><circle cx="6" cy="6" r="5" fill="none" stroke="#1f8c22" stroke-width="2"/></svg>WALLS</li>
  <li><svg viewBox="0 0 12 12"><circle cx="6" cy="6" r="5" fill="none" stroke="#1f8c22" stroke-width="2"/></svg>FIREPLACES</li>
  <li><svg viewBox="0 0 12 12"><circle cx="6" cy="6" r="5" fill="none" stroke="#1f8c22" stroke-width="2"/></svg>TERRACES</li>
  <li><svg viewBox="0 0 12 12"><circle cx="6" cy="6" r="5" fill="none" stroke="#1f8c22" stroke-width="2"/></svg>SMOKERIES</li>
  <li><svg viewBox="0 0 12 12"><circle cx="6" cy="6" r="5" fill="none" stroke="#1f8c22" stroke-width="2"/></svg>PATHS</li>
  <li><svg viewBox="0 0 12 12"><circle cx="6" cy="6" r="5" fill="none" stroke="#1f8c22" stroke-width="2"/></svg>FENCES</li>
  <li><svg viewBox="0 0 12 12"><circle cx="6" cy="6" r="5" fill="none" stroke="#1f8c22" stroke-width="2"/></svg>OUTDOOR KITCHENS</li>
</ul>
<div class="abs service-photo" role="img" aria-label="Gloved hands laying paving stones with a rubber mallet" style="left:666px;top:1132px;width:432px;height:326px;background:linear-gradient(135deg,#9a9a9a,#d8d6d2 50%,#6f6f72)"></div>

<div class="abs service-photo" role="img" aria-label="Craftsman sanding an old wooden chair" style="left:108px;top:1506px;width:432px;height:330px;background:linear-gradient(135deg,#4a5a3a,#9a7a5a 55%,#3b2e26)"></div>
<h3 class="abs heading service-title" style="left:576px;top:1534px">RESTORATION</h3>
<div class="abs service-text" style="left:576px;top:1580px"><p>It's good to see that fixing old things has become popular again in recent years and people are trying to find ways to preserve valuable old windows and pieces of furniture before deciding to replace them.</p><p>It is possible to give a new life to almost any wooden door, window, piece of furniture or staircase. The extensive experience of our craftsmen will help you achieve the desired result.</p></div>
<ul class="abs service-list" style="left:578px;top:1724px">
  <li><svg viewBox="0 0 12 12"><circle cx="6" cy="6" r="5" fill="none" stroke="#1f8c22" stroke-width="2"/></svg>FURNITURE</li>
  <li><svg viewBox="0 0 12 12"><circle cx="6" cy="6" r="5" fill="none" stroke="#1f8c22" stroke-width="2"/></svg>STAIRCASES</li>
  <li><svg viewBox="0 0 12 12"><circle cx="6" cy="6" r="5" fill="none" stroke="#1f8c22" stroke-width="2"/></svg>WINDOWS</li>
  <li><svg viewBox="0 0 12 12"><circle cx="6" cy="6" r="5" fill="none" stroke="#1f8c22" stroke-width="2"/></svg>FLOORS</li>
  <li><svg viewBox="0 0 12 12"><circle cx="6" cy="6" r="5" fill="none" stroke="#1f8c22" stroke-width="2"/></svg>DOORS</li>
  <li><svg viewBox="0 0 12 12"><circle cx="6" cy="6" r="5" fill="none" stroke="#1f8c22" stroke-width="2"/></svg>SPECIAL PROJECTS</li>
</ul>

<!-- About -->
<section class="abs about"></section>
<div class="abs about-people" role="img" aria-label="Two workers with wooden planks and tool belts"></div>
<h2 class="abs heading about-title">ABOUT OUR COMPANY</h2>
<div class="abs about-text">
  <p>Praxelun is a company whose business operations include making wooden products, restoration and building structures from natural stone.</p>
  <p>All of our products are made by craftsmen and specialists who have extensive experience and knowledge in their fields.</p>
  <p>The products we offer are always handmade and we take the requests and ideas of the specific client into account. We always strive to achieve the best possible quality.</p>
</div>
<div class="abs about-sign"><div class="quote">Quality matters,</div><div class="name">Praxelun</div></div>

<!-- Contact -->
<section class="abs contact" role="img" aria-label="Dimmed workshop background"></section>
<h2 class="abs heading section-title contact-title">CONTACT US</h2>
<h3 class="abs heading info-title">CONTACT INFORMATION</h3>
<div class="abs info-row" style="top:2556px">
  <span class="info-icon"><svg width="16" height="18" viewBox="0 0 16 18"><path d="M8 17 C3 11 2 9 2 7 A6 6 0 0 1 14 7 C14 9 13 11 8 17Z" fill="#fff"/><circle cx="8" cy="7" r="2.2" fill="#26221f"/></svg></span>
  <span>Karvelo 12<br>10415 Norrvik ELDORIA</span>
</div>
<div class="abs info-row" style="top:2620px">
  <span class="info-icon"><svg width="18" height="14" viewBox="0 0 18 14"><rect x="1" y="1" width="16" height="12" rx="1" fill="#fff"/><path d="M1 2 L9 8 L17 2" fill="none" stroke="#26221f" stroke-width="1.5"/></svg></span>
  <span>e-mail: hello@praxelun.example</span>
</div>
<div class="abs info-row" style="top:2684px">
  <span class="info-icon"><svg width="16" height="16" viewBox="0 0 16 16"><path d="M3 1 L6 1 L7 5 L5 6.5 C6 9 7 10 9.5 11 L11 9 L15 10 L15 13 C15 14 14 15 13 15 C6 14 2 10 1 3 C1 2 2 1 3 1Z" fill="#fff"/></svg></span>
  <span>Telephone: +000 55 01234</span>
</div>
<div class="abs social-title">SOCIAL</div>
<div class="abs social-icons"><span></span><span></span><span></span><span></span><span></span></div>

<div class="abs field" style="left:426px;top:2502px;width:308px;height:32px">NAME :</div>
<div class="abs field" style="left:742px;top:2502px;width:310px;height:32px">TELEPHONE</div>
<div class="abs field" style="left:426px;top:2542px;width:626px;height:32px">E-MAIL</div>
<div class="abs field" style="left:426px;top:2582px;width:626px;height:234px">MESSAGE :</div>
<a class="abs btn-submit">SUBMIT</a>

<!-- Footer -->
<footer class="abs footer">
  <div class="footer-nav">HOME<span>/</span>ABOUT US<span>/</span>OUR SERVICES<span>/</span>REVIEWS<span>/</span>CONTACT US</div>
  <div class="footer-copy">2016 © Praxelun.example All Rights Reserved</div>
</footer>

</body>
</html>
```